BOLD & MINIMALIST DESIGN NEEDED

We want a very bold but minimalistic business card design that is impactful and utilizes both sides of the business card. Our current logo is included for your use.

We want bold fonts and good use of negative space. We don't want the logo to overpower the design.

Target Market(s)

Professionals who are building new commercial buildings.

Industry/Entity Type

Construction

Contact Information for Business Card

Name, Title, email, office phone, cell phone, website

Font styles to use
Serif
Sans Serif

Requirements
Must have
• Bold design!

```html
<!DOCTYPE html>
<html lang="en">
<head>
<meta charset="utf-8">
<title>Ridgeline Design + Build – Business Card</title>
<link href="https://fonts.googleapis.com/css2?family=Montserrat:wght@400;500;800&family=Oswald:wght@600&display=swap" rel="stylesheet">
<style>
  :root {
    --bg: #3b3431;
    --green: #7ccb1f;
    --green-dark: #6db519;
    --black: #111111;
    --white: #ffffff;
    --text: #1c1c1c;
  }
  * { box-sizing: border-box; margin: 0; padding: 0; }
  html, body { width: 1200px; height: 716px; overflow: hidden; }
  body {
    background: var(--bg);
    position: relative;
    font-family: "Montserrat", sans-serif;
  }
  .card {
    position: absolute;
    top: 203px;
    width: 540px;
    height: 309px;
    overflow: hidden;
  }
  .card-back { left: 40px; background: var(--green); }
  .card-front { left: 620px; background: var(--white); }

  .back-pattern {
    position: absolute; inset: 0;
    background: linear-gradient(135deg, var(--green-dark), var(--green) 60%, #8ad92c);
  }
  .back-mark {
    position: absolute;
    left: 50%; top: 74%;
    transform: translate(-50%, -50%);
    color: var(--white);
    font-weight: 800;
    font-size: 16px;
    letter-spacing: 1px;
  }

  .brand {
    position: absolute;
    left: 40px; top: 44px;
    color: var(--black);
    font-weight: 800;
    font-size: 22px;
    line-height: 1.15;
    letter-spacing: 0.5px;
  }
  .divider {
    position: absolute;
    left: 40px; right: 70px; top: 128px;
    height: 1.5px;
    background: var(--green);
  }
  .contacts {
    position: absolute;
    left: 40px; top: 142px;
    list-style: none;
    font-size: 11.5px;
    color: var(--text);
    line-height: 1.45;
  }
  .contacts li { display: flex; align-items: center; gap: 6px; }
  .contacts svg { width: 10px; height: 10px; fill: var(--green); flex: none; }
  .person {
    position: absolute;
    right: 44px; top: 200px;
    text-align: right;
  }
  .person-name {
    font-family: "Oswald", sans-serif;
    font-weight: 600;
    font-size: 28px;
    color: var(--green);
    line-height: 1;
    border-bottom: 1.5px solid var(--green);
    padding-bottom: 2px;
  }
  .person-title {
    font-size: 11px;
    letter-spacing: 1px;
    color: var(--text);
    margin-top: 3px;
  }
  .band-green {
    position: absolute;
    left: 0; width: 205px; bottom: 22px;
    height: 6px;
    background: var(--green);
  }
  .band-black {
    position: absolute;
    left: 195px; right: 0; bottom: 0;
    height: 26px;
    background: var(--black);
    clip-path: polygon(14px 0, 100% 0, 100% 100%, 0 100%);
    display: flex; align-items: center; justify-content: center;
    font-size: 13px; font-weight: 500;
    color: var(--white);
    letter-spacing: 0.5px;
  }
  .band-black .accent { color: var(--green); }
</style>
</head>
<body>
  <section class="card card-back">
    <div class="back-pattern" role="img" aria-label="Repeating embossed brand pattern in tonal green"></div>
    <div class="back-mark">RIDGELINE</div>
  </section>

  <section class="card card-front">
    <div class="brand">RIDGELINE<br>DESIGN + BUILD</div>
    <div class="divider"></div>
    <ul class="contacts">
      <li><svg viewBox="0 0 24 24"><path d="M6.6 10.8a15 15 0 0 0 6.6 6.6l2.2-2.2c.3-.3.7-.4 1-.2 1.1.4 2.3.6 3.6.6.6 0 1 .4 1 1V20c0 .6-.4 1-1 1A17 17 0 0 1 3 4c0-.6.4-1 1-1h3.5c.6 0 1 .4 1 1 0 1.3.2 2.5.6 3.6.1.3 0 .7-.2 1z"/></svg>(555) 014-2268</li>
      <li><svg viewBox="0 0 24 24"><path d="M3 9c3-4 15-4 18 0l-2 3-4-1V9H9v2l-4 1zm3 5h12l2 7H4z"/></svg>(555) 014-2268</li>
      <li><svg viewBox="0 0 24 24"><path d="M2 5h20v14H2zm2 2v.5l8 5 8-5V7zm0 2.8V17h16V9.8l-8 5z"/></svg>ridgelinebuild@mail.com</li>
    </ul>
    <div class="person">
      <div class="person-name">MARK ELLISON</div>
      <div class="person-title">OWNER</div>
    </div>
    <div class="band-green"></div>
    <div class="band-black">www.<span class="accent">ridgelinebuild</span>.com</div>
  </section>
</body>
</html>
```